Core Values Poster for Technology Business

A core values poster for our office. We don't have much in mind beyond a couple of logos (we have two companies) and then the 4 Core Values we want to present. Mostly, we want this to be simple (easy to take in as a reminder in 5-10 seconds) in a very visually appealing way.

If you can incorporate a high-look-and-feel, great, but not if it over complicates the entire poster/sign.

The core values are:
Relationships Matter
Passion Drives us to Excellence
All About Teamwork
Consistent, Resourceful, Relentless

Our file with both logos together is attached. This is a low-res version. We would provide a high-res version for final production.

Industry/Entity Type

Business

Font styles to use
Serif

Colors
ec1f27
0255a3

Requirements
Nice to have
• This is an update. To be able to incorporate some of our corporate look-and-feel, but not have a black background (as on our kolabrite.net stie), please see the Video Conferencing Slick file that I have uploaded. Might be able to use parts of this type of format to tie in (but not use it exactly as-is - since this is a client facing document).

```html
<!DOCTYPE html>
<html lang="en">
<head>
<meta charset="utf-8">
<title>Core Values Poster</title>
<link href="https://fonts.googleapis.com/css2?family=Bebas+Neue&display=swap" rel="stylesheet">
<style>
  :root {
    --page: #ffffff;
    --night: #0b0b0c;
    --night-soft: #1d1d20;
    --rose: #e5335a;
    --ocean: #3b7eb0;
    --ocean-deep: #2a6a9c;
    --lamp: #f4eda2;
    --snow: #ffffff;
    --logo-ink: #3a3a3a;
    --display: "Bebas Neue", "Oswald", sans-serif;
  }
  * { box-sizing: border-box; margin: 0; padding: 0; }
  html, body { width: 1200px; height: 1000px; overflow: hidden; background: var(--page); }
  .canvas { position: relative; width: 1200px; height: 1000px; font-family: var(--display); }

  .poster { position: absolute; top: 100px; width: 478px; height: 715px; overflow: hidden; }
  .poster--night { left: 84px; --line-a: var(--snow); --line-b: var(--snow); --mark: var(--snow); }
  .poster--light { left: 646px; --line-a: var(--rose); --line-b: var(--ocean); --mark-a: var(--rose); --mark-b: var(--ocean); }
  .poster__art { position: absolute; inset: 0; width: 478px; height: 715px; }

  .brand { position: absolute; color: var(--logo-ink); line-height: 1; display: flex; align-items: center; gap: 5px; }
  .brand--left { left: 14px; top: 18px; }
  .brand--right { left: 292px; top: 27px; }
  .brand__dot { width: 12px; height: 12px; border-radius: 50%; background: var(--rose); }
  .brand__square { width: 12px; height: 12px; background: var(--ocean-deep); }
  .brand__name { font-size: 26px; letter-spacing: .5px; }
  .brand__sub { display: block; font-size: 11px; letter-spacing: .6px; }
  .brand--right .brand__name { font-size: 19px; letter-spacing: .4px; }

  .banner-title { position: absolute; left: 0; width: 478px; top: 112px; text-align: center;
    color: var(--snow); font-size: 56px; letter-spacing: 2px; line-height: 1; }
  .banner-title .cap { font-size: 70px; }

  .value { position: absolute; line-height: .9; white-space: nowrap; }
  .value--a { color: var(--line-a); }
  .value--b { color: var(--line-b); }
  .relationships { left: 181px; top: 226px; font-size: 41px; letter-spacing: .3px; }
  .relationships .cap { font-size: 49px; }
  .matter { left: 180px; top: 258px; font-size: 84px; letter-spacing: .5px; }
  .passion { left: 46px; top: 324px; font-size: 38px; letter-spacing: .5px; }
  .passion .cap { font-size: 48px; }
  .excellence { left: 45px; top: 358px; font-size: 78px; letter-spacing: 1px; }
  .all-about { left: 146px; top: 438px; font-size: 50px; letter-spacing: 15px; }
  .teamwork { left: 142px; top: 480px; font-size: 72px; letter-spacing: 4px; }
  .consistent { left: 48px; top: 542px; font-size: 60px; letter-spacing: 1px; }
  .consistent .cap { font-size: 70px; }
  .resourceful { left: 49px; top: 596px; font-size: 50px; letter-spacing: 2.5px; }
  .relentless { left: 50px; top: 636px; font-size: 56px; letter-spacing: 3px; }

  .icon { position: absolute; border-radius: 14px; }
  .poster--night .icon { background: var(--mark); opacity: .9; }
  .poster--light .icon--a { background: var(--mark-a); opacity: .85; }
  .poster--light .icon--b { background: var(--mark-b); opacity: .85; }
  .icon--hearts { left: 51px; top: 246px; width: 108px; height: 58px; border-radius: 30px; }
  .icon--trophy { left: 371px; top: 338px; width: 60px; height: 76px; }
  .icon--team { left: 41px; top: 420px; width: 98px; height: 112px; }
  .icon--network { left: 296px; top: 556px; width: 130px; height: 120px; border-radius: 50%; }
</style>
</head>
<body>
<main class="canvas">

  <section class="poster poster--night" aria-label="Core values poster, dark edition">
    <svg class="poster__art" viewBox="0 0 478 715" aria-hidden="true">
      <defs>
        <linearGradient id="fade-night" x1="0" y1="0" x2="0" y2="1">
          <stop offset="0" stop-color="#ffffff"/>
          <stop offset=".09" stop-color="#ffffff"/>
          <stop offset=".17" stop-color="#1d1d20"/>
          <stop offset="1" stop-color="#0b0b0c"/>
        </linearGradient>
      </defs>
      <rect width="478" height="715" fill="url(#fade-night)" role="img" aria-label="Starry night sky texture"/>
      <path d="M0,92 Q239,48 478,92 L478,110 Q239,66 0,110 Z" fill="var(--rose)"/>
      <path d="M0,120 Q239,90 478,120 L478,200 Q239,160 0,200 Z" fill="var(--ocean)"/>
      <path d="M0,210 Q239,170 478,210 L478,230 Q239,184 0,230 Z" fill="var(--rose)"/>
      <circle cx="74" cy="150" r="8" fill="var(--lamp)"/>
      <circle cx="404" cy="150" r="8" fill="var(--lamp)"/>
    </svg>

    <div class="brand brand--left"><span class="brand__dot"></span><span class="brand__name">Vantora<span class="brand__sub">Technology Solutions</span></span></div>
    <div class="brand brand--right"><span class="brand__square"></span><span class="brand__name">Bastion Security Group</span></div>

    <h1 class="banner-title"><span class="cap">C</span>ORE <span class="cap">V</span>ALUES</h1>

    <div class="icon icon--hearts" role="img" aria-label="Two linked hearts icon"></div>
    <p class="value value--a relationships"><span class="cap">R</span>ELATIONSHIPS</p>
    <p class="value value--a matter">MATTER</p>

    <p class="value value--b passion"><span class="cap">P</span>ASSION <span class="cap">D</span>RIVES US TO</p>
    <p class="value value--b excellence">EXCELLENCE</p>
    <div class="icon icon--trophy" role="img" aria-label="Trophy held on an open hand icon"></div>

    <div class="icon icon--team" role="img" aria-label="Two teammates raising a trophy icon"></div>
    <p class="value value--a all-about">ALL ABOUT</p>
    <p class="value value--a teamwork">TEAMWORK</p>

    <p class="value value--b consistent"><span class="cap">C</span>ONSISTENT</p>
    <p class="value value--b resourceful">RESOURCEFUL</p>
    <p class="value value--b relentless">RELENTLESS</p>
    <div class="icon icon--network" role="img" aria-label="Team, growth chart and gear connected icon"></div>
  </section>

  <section class="poster poster--light" aria-label="Core values poster, light panel edition">
    <svg class="poster__art" viewBox="0 0 478 715" aria-hidden="true">
      <defs>
        <linearGradient id="fade-light" x1="0" y1="0" x2="0" y2="1">
          <stop offset="0" stop-color="#ffffff"/>
          <stop offset=".09" stop-color="#ffffff"/>
          <stop offset=".17" stop-color="#1d1d20"/>
          <stop offset="1" stop-color="#0b0b0c"/>
        </linearGradient>
      </defs>
      <rect width="478" height="715" fill="url(#fade-light)" role="img" aria-label="Starry night sky texture"/>
      <path d="M0,92 Q239,48 478,92 L478,110 Q239,66 0,110 Z" fill="var(--rose)"/>
      <path d="M0,120 Q239,90 478,120 L478,200 Q239,160 0,200 Z" fill="var(--ocean)"/>
      <path d="M0,210 Q239,170 478,210 L478,230 Q239,184 0,230 Z" fill="var(--rose)"/>
      <circle cx="74" cy="150" r="8" fill="var(--lamp)"/>
      <circle cx="404" cy="150" r="8" fill="var(--lamp)"/>
      <path d="M22,242 Q239,198 456,242 L456,695 L22,695 Z" fill="#ffffff" stroke="var(--rose)" stroke-width="3"/>
    </svg>

    <div class="brand brand--left"><span class="brand__dot"></span><span class="brand__name">Vantora<span class="brand__sub">Technology Solutions</span></span></div>
    <div class="brand brand--right"><span class="brand__square"></span><span class="brand__name">Bastion Security Group</span></div>

    <h2 class="banner-title"><span class="cap">C</span>ORE <span class="cap">V</span>ALUES</h2>

    <div class="icon icon--hearts icon--a" role="img" aria-label="Two linked hearts icon"></div>
    <p class="value value--a relationships"><span class="cap">R</span>ELATIONSHIPS</p>
    <p class="value value--a matter">MATTER</p>

    <p class="value value--b passion"><span class="cap">P</span>ASSION <span class="cap">D</span>RIVES US TO</p>
    <p class="value value--b excellence">EXCELLENCE</p>
    <div class="icon icon--trophy icon--b" role="img" aria-label="Trophy held on an open hand icon"></div>

    <div class="icon icon--team icon--a" role="img" aria-label="Two teammates raising a trophy icon"></div>
    <p class="value value--a all-about">ALL ABOUT</p>
    <p class="value value--a teamwork">TEAMWORK</p>

    <p class="value value--b consistent"><span class="cap">C</span>ONSISTENT</p>
    <p class="value value--b resourceful">RESOURCEFUL</p>
    <p class="value value--b relentless">RELENTLESS</p>
    <div class="icon icon--network icon--b" role="img" aria-label="Team, growth chart and gear connected icon"></div>
  </section>

</main>
</body>
</html>
```